New Corporate Email Signature with Custom GIF KAV Electric LLC & KAV Fire & Security

Project Overview
KAV Electric LLC and KAV Fire & Security are seeking a professional, polished, and technically robust corporate email signature design. The project has two integrated deliverables:
A custom animated GIF representing both sides of our business
A complete corporate email signature layout designed for real-world compatibility (Gmail, Outlook, iOS, Android)
Our brand aesthetic is corporate, conservative, and clean. We value clarity, trust, professionalism, and subtle creativity β€” nothing overly flashy or cartoonish.
This design will be used across the entire company and must be visually aligned with our brand while remaining technically dependable.

PART 1 β€” Animated GIF Requirements
The GIF will be the core visual anchor of the new signature.
It must be clean, smooth, subtle, and optimized for email use.
βš™ Technical Requirements
Max file size: 150–200 KB (smaller is better)
Dimensions: approx 300px width (flexible, but must look good small)
Looping: continuous loop
Style: professional, minimalistic transitions

No rapid flashing or harsh animations
Must export cleanly into a format email clients accept

🎞 GIF Animation Sequence
Phase 1 β€” KAV Electric (KE)
Use the yellow β€œKE” avatar logo (provided).
Animation flow:
KE avatar appears
Full name β€œKAV Electric LLC” slides in, fades in, or otherwise appears smoothly
A scrolling or cycling list of service offerings displays:
EV Charging Stations
Generator & Transformers
Testing & Troubleshooting
LED Lighting Upgrades
After the list is shown, the entire KE segment fades out

Phase 2 β€” KAV Fire & Security (KF)
Use the red β€œKF” avatar logo (provided).
Animation flow mirrors Phase 1:
KF avatar appears
Full name β€œKAV Fire & Security” slides/fades in
Scrolling or cycling list of services displays:
Fire Alarm Upgrades
BQTL 48 Test & Inspect
Security Surveillance Systems
Access Control Systems
Data & Fiber Optic Cabling
Fade out β†’ loop back to KE
Creative Direction

Designers are encouraged to use:
Clean transitions
Soft fades
Professional typography
Modern minimalism
Consistent brand colors
High clarity at small sizes

Avoid:
Busy motion
Hard flashes
Excessive text overlays
Overly long transitions

The goal: a smooth, corporate-grade rotation that fits seamlessly into an email signature.

PART 2 β€” Corporate Email Signature Design

The signature must be visually appealing, brand-aligned, and structurally bulletproof across all major email systems.
πŸ“ Required Elements
πŸ‘€ Left Side Content
Circular headshot (we will supply final photos)
Social media icons with embedded URLs:
Facebook
LinkedIn
Google Business Profile
Instagram

Icons should be clean, modern, and in alignment with brand colors
πŸ“„ Right Side Content
Name
Title
KAV Electric LLC / KAV Fire & Security (depending on user)
Phone number
Email address
License# 52804
Physical office address: 384 Pembrook St, Westwood NJ 07912

Small CTA for newsletter signup (button or micro-banner)

🏒 Branding Assets Provided

You will receive:
KE avatar logo
KF avatar logo
Full-name KE logo
Full-name KF logo

These should be incorporated naturally and professionally.

Design Requirements

Conservative corporate styling

Clean typography

Balanced use of white space

Professional hierarchy

Light and dark mode compatibility preferred

Layout should not rely on one large image

All images should export cleanly for hosting on servers/CDN

Avoid overly tall signatures

The final signature must present as modern, trustworthy, and technically reliable across platforms.

πŸ§ͺ Compatibility Requirements

The signature must display correctly in:

Gmail (web and mobile)

Outlook (desktop & online)

Apple Mail

iPhone Mail

Android mail apps

Designers must avoid DIV-based layouts and instead propose a layout that can be implemented using table-based HTML, which is the industry standard for email compatibility.

You do not need to build the HTML β€” only supply the final layered design (PSD/AI/Figma) plus a clear structural layout that can be converted to HTML later.

πŸ“¦ Deliverables
1. Animated GIF

Final optimized GIF

Source file (After Effects, Photoshop, or equivalent)

Export guidelines so we can reproduce future versions

2. Email Signature Design

Full static design mockup

Modular layout for each employee

Icon set for social media

Newsletter CTA element

Clear spacing, alignment, and typography specifications

All source files (PSD, AI, Figma, etc.)

🧭 Creative Guidance Summary

We want:
βœ” Modern
βœ” Corporate
βœ” Minimalistic
βœ” Professional
βœ” Clean motion
βœ” Consistent branding
βœ” Email-safe elements

We do not want:
✘ Flashy marketing look
✘ Overly colorful or playful styles
✘ Hard-to-read fonts
✘ Heavy animation
✘ Oversized signatures

πŸ›  Tools & Format Flexibility

We allow full creative freedom regarding:

Animation style

Typography choices

Structuring of the two-column layout

How the service lists scroll or cycle

As long as the end result is clean, brand-aligned, professional, and email-compatible.

πŸ’¬ Final Note to Designers

We encourage creativity within the boundaries of corporate professionalism.
This signature will represent our company every time an email is sent β€” it must communicate trust, clarity, expertise, and brand strength.

```html
<!DOCTYPE html>
<html lang="en">
<head>
<meta charset="utf-8">
<title>KAV Fire &amp; Security – Email Signature</title>
<link rel="stylesheet" href="https://fonts.googleapis.com/css2?family=Open+Sans:wght@400;600;700;800&display=swap">
<style>
  :root {
    --brand-red: #e2202a;
    --brand-red-soft: #fde3e4;
    --ink: #1f1f1f;
    --ink-muted: #3a3a3a;
    --stripe-grey: #b5b5b5;
    --panel-grey: #ececec;
    --button-grey: #7a7a7a;
    --rule-grey: #9a9a9a;
    --paper: #ffffff;
  }
  html, body {
    margin: 0;
    padding: 0;
    width: 1200px;
    height: 300px;
    overflow: hidden;
    background: var(--paper);
    font-family: "Open Sans", Arial, sans-serif;
  }
  .signature {
    position: relative;
    width: 1200px;
    height: 300px;
    overflow: hidden;
    background: var(--paper);
  }
  .backdrop {
    position: absolute;
    inset: 0;
  }
  .headshot {
    position: absolute;
    left: 84px;
    top: 14px;
    width: 210px;
    height: 210px;
    border-radius: 50%;
    border: 8px solid #d2d2d2;
    background: radial-gradient(circle at 50% 38%, #d9c2a8 0%, #b9a58e 40%, #8c8d8f 100%);
    box-sizing: border-box;
  }
  .brand-name {
    position: absolute;
    left: 360px;
    top: 10px;
    margin: 0;
    font-size: 34px;
    font-weight: 800;
    letter-spacing: 1px;
    color: var(--brand-red);
    text-transform: uppercase;
  }
  .person-name {
    position: absolute;
    left: 366px;
    top: 74px;
    margin: 0;
    font-size: 29px;
    font-weight: 700;
    color: var(--ink);
  }
  .person-title {
    position: absolute;
    left: 366px;
    top: 120px;
    margin: 0;
    font-size: 20px;
    font-weight: 400;
    color: var(--ink-muted);
  }
  .title-rule {
    position: absolute;
    left: 366px;
    top: 164px;
    width: 186px;
    height: 2px;
    background: var(--rule-grey);
  }
  .contact {
    position: absolute;
    display: flex;
    align-items: center;
    gap: 14px;
    font-size: 20px;
    color: var(--ink);
  }
  .contact-icon {
    width: 30px;
    height: 30px;
    flex: none;
  }
  .contact--phone   { left: 366px; top: 186px; }
  .contact--email   { left: 636px; top: 186px; }
  .contact--license { left: 366px; top: 238px; }
  .contact--address { left: 636px; top: 238px; }
  .newsletter-button {
    position: absolute;
    left: 842px;
    top: 66px;
    width: 316px;
    height: 70px;
    border-radius: 35px;
    background: var(--button-grey);
    color: var(--paper);
    font-size: 24px;
    font-weight: 600;
    display: flex;
    align-items: center;
    justify-content: center;
    text-decoration: none;
    box-shadow: 0 2px 6px rgba(0,0,0,0.18);
  }
  .social-links {
    position: absolute;
    left: 64px;
    top: 244px;
    display: flex;
    gap: 20px;
  }
  .social-link {
    width: 32px;
    height: 32px;
    border-radius: 50%;
    border: 3px solid var(--paper);
    box-sizing: border-box;
    display: block;
  }
</style>
</head>
<body>
  <main class="signature">
    <svg class="backdrop" width="1200" height="300" viewBox="0 0 1200 300" aria-hidden="true">
      <!-- left brand wave -->
      <path d="M0 96 C70 70 170 70 250 112 L400 180 L322 300 L0 300 Z" fill="var(--brand-red)"/>
      <!-- diagonal accent stripe -->
      <polygon points="316,300 342,300 452,158 426,158" fill="var(--stripe-grey)"/>
      <!-- top-right panels -->
      <path d="M850 0 L1200 0 L1200 156 C1090 110 960 60 850 0 Z" fill="var(--panel-grey)"/>
      <path d="M990 0 L1200 0 L1200 84 C1120 60 1050 34 990 0 Z" fill="var(--brand-red)"/>
      <!-- bottom-right corner -->
      <polygon points="1120,300 1200,216 1200,232 1136,300" fill="var(--stripe-grey)"/>
      <polygon points="1150,300 1200,246 1200,300" fill="var(--brand-red)"/>
    </svg>

    <div class="headshot" role="img" aria-label="Circular headshot of the team member"></div>

    <h1 class="brand-name">KAV Fire &amp; Security</h1>

    <h2 class="person-name">John</h2>
    <p class="person-title">Project Manager</p>
    <div class="title-rule"></div>

    <div class="contact contact--phone">
      <svg class="contact-icon" viewBox="0 0 30 30" aria-hidden="true">
        <circle cx="15" cy="15" r="15" fill="var(--brand-red-soft)"/>
        <path d="M10 8.5 L12.5 8 L14 11.5 L12.4 12.8 C13.2 14.6 14.8 16.4 16.8 17.4 L18 15.8 L21.5 17.2 L21 19.8 C20.6 21 19.4 21.6 18 21.3 C13.4 20.2 9.6 16.4 8.7 11.8 C8.5 10.4 9 9 10 8.5 Z" fill="var(--brand-red)"/>
      </svg>
      <span>+1 888 888 8888</span>
    </div>

    <div class="contact contact--email">
      <svg class="contact-icon" viewBox="0 0 30 30" aria-hidden="true">
        <circle cx="15" cy="15" r="15" fill="var(--brand-red-soft)"/>
        <rect x="8" y="10" width="14" height="10" rx="1.5" fill="var(--brand-red)"/>
        <path d="M8.5 10.8 L15 15.6 L21.5 10.8" fill="none" stroke="var(--brand-red-soft)" stroke-width="1.4"/>
      </svg>
      <span>support@kavfiresecurity.com</span>
    </div>

    <div class="contact contact--license">
      <svg class="contact-icon" viewBox="0 0 30 30" aria-hidden="true">
        <circle cx="15" cy="15" r="15" fill="var(--brand-red-soft)"/>
        <rect x="9.5" y="7.5" width="11" height="15" rx="1.2" fill="var(--brand-red)"/>
        <rect x="11.5" y="11" width="7" height="1.4" fill="var(--brand-red-soft)"/>
        <rect x="11.5" y="14" width="7" height="1.4" fill="var(--brand-red-soft)"/>
        <rect x="11.5" y="17" width="4.5" height="1.4" fill="var(--brand-red-soft)"/>
      </svg>
      <span>License# 52804</span>
    </div>

    <div class="contact contact--address">
      <svg class="contact-icon" viewBox="0 0 30 30" aria-hidden="true">
        <circle cx="15" cy="15" r="15" fill="var(--brand-red-soft)"/>
        <path d="M15 7 C11.7 7 9.5 9.4 9.5 12.4 C9.5 16.4 15 23 15 23 C15 23 20.5 16.4 20.5 12.4 C20.5 9.4 18.3 7 15 7 Z" fill="var(--brand-red)"/>
        <circle cx="15" cy="12.4" r="2.2" fill="var(--brand-red-soft)"/>
      </svg>
      <span>384 Pembrook St, Westwood NJ 07912</span>
    </div>

    <a class="newsletter-button" href="#newsletter">Join Our Newslatter</a>

    <nav class="social-links" aria-label="Social profiles">
      <a class="social-link" href="#social-1" aria-label="Social profile 1"></a>
      <a class="social-link" href="#social-2" aria-label="Social profile 2"></a>
      <a class="social-link" href="#social-3" aria-label="Social profile 3"></a>
      <a class="social-link" href="#social-4" aria-label="Social profile 4"></a>
    </nav>
  </main>
</body>
</html>
```